Falkrin homes and renovations business card design.

Would like some new card designs utilizing my new logo that look professional. I am open to different colors on the logo or utilize the same ones we have. I like the original concept but would like to see some fresh ideas and build on what we have already done.

Target Market(s)

Custom home building industry, Real estate sales, Renovation projects.

Industry/Entity Type

Home Builder

Contact Information for Business Card

Falkrin Homes and Renovations
2871 96th Avenue
Brindlecove, Norvale
T2R3W8
Home : 403- 718-4063 Cell: 403- 294-5170

My info is : Dax Falkrin, President and CEO
email: falkrinhomes@maildrop-example.net
Website: falkrinhomes-example.com
websit

Requirements
Must have
• Must Use my new logo design. I am open to different colors on the logo or utilize the same ones in the existing design. I can upload the original logo design if needed.

```html
<!DOCTYPE html>
<html lang="en">
<head>
<meta charset="utf-8">
<title>Falkrin Homes and Renovations – Business Card</title>
<link rel="stylesheet" href="https://fonts.googleapis.com/css2?family=Source+Sans+3:wght@400;600;700&display=swap">
<style>
  :root {
    --backdrop: #1a1a1a;
    --card-white: #ffffff;
    --accent-yellow: #fbba1f;
    --brand-gold: #b5873a;
    --ink: #111111;
    --rule: #e6d3a8;
  }
  html, body {
    margin: 0;
    padding: 0;
    width: 1200px;
    height: 900px;
    overflow: hidden;
    background: var(--backdrop);
  }
  .canvas {
    position: relative;
    width: 1200px;
    height: 900px;
    font-family: "Source Sans 3", sans-serif;
  }
  .card {
    position: absolute;
    top: 206px;
    width: 275px;
    height: 445px;
  }
  .card--front { left: 315px; background: var(--card-white); }
  .card--back  { left: 635px; background: var(--brand-gold); }

  .tab {
    position: absolute;
    left: 72px;
    width: 114px;
    height: 23px;
    background: var(--accent-yellow);
  }
  .tab--top { top: 0; }
  .tab--bottom { bottom: 0; }

  .brand {
    position: absolute;
    left: 0;
    right: 0;
    text-align: center;
    font-weight: 700;
    font-size: 24px;
    line-height: 1.1;
    letter-spacing: 0.4px;
    text-transform: uppercase;
    white-space: nowrap;
  }
  .brand__mark {
    display: block;
    width: 14px;
    height: 14px;
    margin: 0 auto 12px;
  }
  .card--front .brand { top: 86px; color: var(--brand-gold); }
  .card--front .brand__mark { background: var(--brand-gold); }
  .card--back .brand { top: 180px; color: var(--card-white); }
  .card--back .brand__mark { background: var(--card-white); }

  .person {
    position: absolute;
    top: 224px;
    left: 0;
    right: 0;
    text-align: center;
  }
  .person__name {
    margin: 0;
    font-size: 23px;
    font-weight: 700;
    color: var(--accent-yellow);
    line-height: 1;
    letter-spacing: 0.2px;
  }
  .person__title {
    margin: 3px 0 0 -22px;
    font-size: 12.5px;
    font-weight: 600;
    color: var(--ink);
  }

  .contact {
    position: absolute;
    top: 272px;
    left: 0;
    right: 0;
    margin: 0;
    padding: 0;
    list-style: none;
    text-align: center;
    font-size: 12.5px;
    color: var(--ink);
    line-height: 17px;
  }
  .contact__label { color: var(--brand-gold); font-weight: 600; }

  .divider {
    position: absolute;
    top: 342px;
    left: 30px;
    width: 213px;
    height: 1px;
    background: var(--rule);
  }

  .address {
    position: absolute;
    top: 348px;
    left: 0;
    right: 0;
    text-align: center;
    font-style: normal;
    font-size: 12.5px;
    line-height: 16px;
    color: var(--ink);
  }
  .address__company { color: var(--brand-gold); font-weight: 600; font-size: 13px; }
</style>
</head>
<body>
<main class="canvas">
  <section class="card card--front" aria-label="Business card front">
    <div class="tab tab--top"></div>

    <div class="brand">
      <span class="brand__mark"></span>
      Falkrin Homes<br>and Renovations
    </div>

    <div class="person">
      <p class="person__name">DAX FALKRIN</p>
      <p class="person__title">President and CEO</p>
    </div>

    <ul class="contact">
      <li><span class="contact__label">P:</span> 403- 718-4063</li>
      <li><span class="contact__label">M:</span> 403- 294-5170</li>
      <li><span class="contact__label">E:</span> falkrinhomes@maildrop-example.net</li>
      <li>www.falkrinhomes-example.com</li>
    </ul>

    <div class="divider"></div>

    <address class="address">
      <div class="address__company">Falkrin Homes and Renovations</div>
      <div>2871 96th Avenue</div>
      <div>Brindlecove, Norvale ,T2R3W8</div>
    </address>

    <div class="tab tab--bottom"></div>
  </section>

  <section class="card card--back" aria-label="Business card back">
    <div class="brand">
      <span class="brand__mark"></span>
      Falkrin Homes<br>and Renovations
    </div>
  </section>
</main>
</body>
</html>
```